Dusty Spur Outfitters Home Page

I need a logo and page design for my home page, maybe some background color suggestions to go with it. I want the logo to project "vintage" and "western wear" but not be your typical trite western saddle and gun type thing.
http://www.dustyspuroutfitters.example/store/cart.php
Not looking for page coding just logo and other design elements to lay in over the site's template to make it "pop"
Reason: Have to finalize the design.
Target Market(s)
My customers are 70/30 men to women.
Industry/Entity Type
Gun

```html
<!DOCTYPE html>
<html lang="en">
<head>
<meta charset="utf-8">
<title>Dusty Spur Outfitters</title>
<link href="https://fonts.googleapis.com/css2?family=PT+Sans+Narrow:wght@400;700&family=Open+Sans:wght@400;600&family=Rokkitt:wght@600&display=swap" rel="stylesheet">
<style>
:root{
  --red:#8e1518;
  --red-dark:#6d0f12;
  --red-btn:#a3161b;
  --beige:#ebe4d8;
  --beige-light:#f1ece2;
  --card:#e9e3da;
  --ink:#2b2220;
  --muted:#6b5f55;
  --wood:#a8641f;
  --wood-dark:#5a2f0d;
  --gold:#f0a821;
  --green:#8fd42a;
}
*{margin:0;padding:0;box-sizing:border-box}
html,body{width:795px;height:1200px;overflow:hidden}
body{position:relative;font-family:"Open Sans",sans-serif;color:var(--ink);background:var(--beige)}
.abs{position:absolute}
.topbar{left:0;top:0;width:795px;height:68px;background:linear-gradient(#9a1c1e,#841417)}
.navbar{left:0;top:68px;width:795px;height:40px;background:linear-gradient(#f2ede4,#e2dacd);border-bottom:1px solid #cfc5b5}
.cart-icon{left:120px;top:23px;width:28px;height:28px;border-radius:50%;background:#7a1114;display:flex;align-items:center;justify-content:center}
.cart-text{left:158px;top:21px;color:#f6e9e2;font-size:11px;line-height:16px}
.cart-text b{font-weight:400;font-size:12px;display:block}
.search{left:547px;top:20px;width:131px;height:29px;background:linear-gradient(#fff,#e8e8e8);border:2px solid #c9c9c9}
.search svg{position:absolute;right:8px;top:6px}
.nav a{position:absolute;top:80px;font-family:"PT Sans Narrow",sans-serif;font-size:15px;color:#4a3b33;text-decoration:none}
.brand{left:322px;top:30px;width:153px;height:96px;background:var(--beige-light);border:3px solid #6e5a43;border-radius:10px;display:flex;align-items:center;justify-content:center;text-align:center;font-family:"PT Sans Narrow",sans-serif;font-weight:700;font-size:22px;line-height:24px;color:#5b3b1c}
.wood{left:0;top:108px;width:795px;height:935px;background:radial-gradient(ellipse at 50% 40%,#c98535 0%,#a8641f 45%,#6e3a10 100%)}
.hero{left:120px;top:145px;width:556px;height:291px;border:2px solid #e9e4dc;background:linear-gradient(160deg,#9b9a95 0%,#b8a98f 45%,#8b8a86 100%)}
.arrow{width:31px;height:29px;border:1px solid #fff;display:flex;align-items:center;justify-content:center}
.cat{left:120px;top:455px;width:136px}
.cat h3,.feat h3{font-family:"PT Sans Narrow",sans-serif;color:#fff;font-weight:700}
.cat h3{background:var(--red);height:29px;line-height:29px;padding-left:13px;font-size:15px}
.cat ul{list-style:none;background:var(--beige)}
.cat li{height:22.7px;line-height:22px;font-size:8px;color:#6a5e55;padding-left:13px;border-bottom:1px solid #ddd5c8}
.cat li span{color:#9a8e83;margin-right:10px}
.sub{left:120px;top:797px;width:136px;height:143px;background:var(--red);text-align:center;color:#fff}
.sub h4{font-family:"PT Sans Narrow",sans-serif;font-weight:700;font-size:15px;line-height:17px;margin-top:17px}
.sub .field{margin:13px auto 0;width:115px;height:27px;background:#fff;font-size:6.5px;color:#555;text-align:left;padding-left:9px;line-height:27px}
.sub .btn{margin:14px auto 0;width:74px;height:22px;background:linear-gradient(#4a4a4a,#2a2a2a);border-radius:2px;font-size:11px;line-height:22px}
.feat{left:275px;top:455px;width:401px;height:27px;background:var(--red)}
.feat h3{font-size:13px;line-height:27px;padding-left:9px;font-weight:400}
.feat .ctl{position:absolute;top:6px;width:15px;height:15px;border:1px solid #d9a3a3;border-radius:50%}
.card{width:126px;height:212px;background:var(--card)}
.card .ph{position:absolute;left:5px;top:3px;width:116px;height:120px}
.card .name{position:absolute;left:11px;top:139px;font-size:9px}
.card .price{position:absolute;left:11px;top:161px;font-size:8.5px}
.card .stars{position:absolute;left:79px;top:160px;font-size:7px;letter-spacing:-0.5px;color:var(--gold)}
.card .stars i{font-style:normal;color:#c9c2b8}
.card .add{position:absolute;left:28px;top:181px;width:73px;height:20px;background:var(--red-btn);border-radius:2px;color:#fff;font-size:8px;line-height:20px;padding-left:6px}
.card .add svg{position:absolute;right:6px;top:5px}
.promo{top:958px;height:68px;border:1px solid #c48a47;border-top:none}
.promo .t{position:absolute;font-family:"Rokkitt",serif;font-weight:600;font-size:16px;color:var(--green);border-bottom:1px solid #b8d98b;line-height:18px}
.promo .s{position:absolute;font-size:7.5px;color:#c99b62}
.foot{left:0;top:1043px;width:795px;height:157px;background:var(--beige-light)}
.col h5{font-weight:400;font-size:10.5px;color:#2b2220;margin-bottom:10px}
.col p{font-size:7px;color:#2b2220;line-height:13.7px}
.pay{width:29px;height:18px;border-radius:2px}
.copy{left:116px;top:1169px;font-size:7.5px;color:#333}
.soc{top:1167px;width:13px;height:13px;border-radius:50%}
.rule{left:0;top:1150px;width:795px;height:1px;background:#ded6c9}
</style>
</head>
<body>
<div class="abs topbar"></div>
<div class="abs navbar"></div>
<div class="abs cart-icon"><svg width="14" height="12" viewBox="0 0 14 12"><path d="M1 1h2l2 7h7l1-5H4" fill="none" stroke="#f4e3dc" stroke-width="1.3"/><circle cx="6" cy="10.5" r="1" fill="#f4e3dc"/><circle cx="11" cy="10.5" r="1" fill="#f4e3dc"/></svg></div>
<div class="abs cart-text"><b>Shopping Cart</b>Item - $0.00</div>
<div class="abs search"><svg width="12" height="12" viewBox="0 0 12 12"><circle cx="7" cy="5" r="3.5" fill="none" stroke="#bbb" stroke-width="1.3"/><path d="M4.5 7.5L1.5 10.5" stroke="#bbb" stroke-width="1.5"/></svg></div>
<nav class="nav">
  <a style="left:119px">Home</a><a style="left:181px">Shipping</a><a style="left:255px">Returns</a>
  <a style="left:497px">About Us</a><a style="left:577px">Sizing</a><a style="left:640px">Contact</a>
</nav>
<div class="abs brand">Dusty Spur<br>Outfitters</div>

<div class="abs wood"></div>
<div class="abs hero" role="img" aria-label="Photo of worn suede cowboy boots on a weathered wooden porch with fallen yellow leaves"></div>
<div class="abs arrow" style="left:630px;top:301px"><svg width="8" height="14"><path d="M7 1L1 7l6 6" fill="none" stroke="#fff"/></svg></div>
<div class="abs arrow" style="left:630px;top:335px"><svg width="8" height="14"><path d="M1 1l6 6-6 6" fill="none" stroke="#fff"/></svg></div>

<aside class="abs cat">
  <h3>Categories</h3>
  <ul>
    <li><span>›</span>Boots</li><li><span>›</span>Men's Western Wear</li><li><span>›</span>Women's Western Wear</li>
    <li><span>›</span>Brand New Arrivals</li><li><span>›</span>CLEARANCE</li><li><span>›</span>T-Shirts</li>
    <li><span>›</span>Vests</li><li><span>›</span>Accessories</li><li><span>›</span>Jackets</li>
    <li><span>›</span>BELTS</li><li><span>›</span>Hand Bags</li><li><span>›</span>Leather</li><li><span>›</span>On Sale!</li>
  </ul>
</aside>
<div class="abs sub">
  <h4>Subscribe to our<br>mailing list</h4>
  <div class="field">Subscribe to our Newsletter!</div>
  <div class="btn">Subscribe</div>
</div>

<div class="abs feat"><h3>FEATURED PRODUCTS</h3><span class="ctl" style="left:354px"></span><span class="ctl" style="left:377px"></span></div>

<div class="abs card" style="left:275px;top:501px"><div class="ph" role="img" aria-label="Man in black embroidered western shirt" style="background:linear-gradient(#e9e3da,#3a302c)"></div><div class="name">Men's Western Wear</div><div class="price">$119.50</div><div class="stars">★★★<i>★★</i></div><div class="add">Add To Cart<svg width="10" height="9"><path d="M0 2h10L8 8H2z" fill="#fff"/></svg></div></div>
<div class="abs card" style="left:413px;top:501px"><div class="ph" role="img" aria-label="Tan lace-up leather boots" style="background:linear-gradient(#e9e3da,#a89378,#e9e3da)"></div><div class="name">Boots</div><div class="price">$119.50</div><div class="stars">★★★<i>★★</i></div><div class="add">Add To Cart<svg width="10" height="9"><path d="M0 2h10L8 8H2z" fill="#fff"/></svg></div></div>
<div class="abs card" style="left:551px;top:501px"><div class="ph" role="img" aria-label="Woman in black embroidered western blouse" style="background:linear-gradient(#e9e3da,#2d2220)"></div><div class="name">Women's Western Wear</div><div class="price">$119.50</div><div class="stars">★★★<i>★★</i></div><div class="add">Add To Cart<svg width="10" height="9"><path d="M0 2h10L8 8H2z" fill="#fff"/></svg></div></div>
<div class="abs card" style="left:275px;top:728px"><div class="ph" role="img" aria-label="Two leather hand bags" style="background:linear-gradient(#e9e3da 30%,#6f5a48)"></div><div class="name">Hand Bags</div><div class="price">$119.50</div><div class="stars">★★★<i>★★</i></div><div class="add">Add To Cart<svg width="10" height="9"><path d="M0 2h10L8 8H2z" fill="#fff"/></svg></div></div>
<div class="abs card" style="left:413px;top:728px"><div class="ph" role="img" aria-label="Black short sleeve t-shirt" style="background:linear-gradient(#2a2a2a,#1a1a1a)"></div><div class="name">Short Sleeves</div><div class="price">$119.50</div><div class="stars">★★★<i>★★</i></div><div class="add">Add To Cart<svg width="10" height="9"><path d="M0 2h10L8 8H2z" fill="#fff"/></svg></div></div>
<div class="abs card" style="left:551px;top:728px"><div class="ph" role="img" aria-label="Olive canvas field jacket" style="background:linear-gradient(#e9e3da,#8a8166,#e9e3da)"></div><div class="name">Jackets</div><div class="price">$119.50</div><div class="stars">★★★<i>★★</i></div><div class="add">Add To Cart<svg width="10" height="9"><path d="M0 2h10L8 8H2z" fill="#fff"/></svg></div></div>

<div class="abs promo" style="left:120px;width:260px">
  <svg class="abs" style="left:46px;top:15px" width="40" height="26" viewBox="0 0 40 26"><rect x="12" y="2" width="26" height="16" fill="none" stroke="#d9b58a" stroke-width="2"/><path d="M12 8H5l-4 6v5h11" fill="none" stroke="#d9b58a" stroke-width="2"/><circle cx="8" cy="21" r="3" fill="#d9b58a"/><circle cx="30" cy="21" r="3" fill="#d9b58a"/></svg>
  <div class="t" style="left:95px;top:18px">FREE SHIPPING</div>
  <div class="s" style="left:95px;top:39px">On Order Over $30 offer today</div>
</div>
<div class="abs promo" style="left:415px;width:261px">
  <svg class="abs" style="left:60px;top:15px" width="32" height="30" viewBox="0 0 32 30"><path d="M6 2c-4 0-5 4-5 13s1 13 5 13" fill="none" stroke="#d9b58a" stroke-width="4"/><rect x="12" y="4" width="18" height="22" rx="2" fill="none" stroke="#d9b58a" stroke-width="2"/><rect x="15" y="8" width="12" height="5" fill="#d9b58a"/></svg>
  <div class="t" style="left:101px;top:18px">GIVE US CALL</div>
  <div class="s" style="left:101px;top:39px">1-800-Spurs (1-800-555-0142)</div>
</div>

<footer class="abs foot"></footer>
<div class="abs col" style="left:121px;top:1062px"><h5>Information</h5><p>Contact us<br>Terms and conditions of use<br>About us<br>Sitemap</p></div>
<div class="abs col" style="left:297px;top:1061px"><h5 style="color:#6b5f55">Customer Support</h5><p style="color:#555">About Us<br>Delivery Information<br>Privacy Policy<br>Term &amp; Condition</p></div>
<div class="abs col" style="left:455px;top:1062px"><h5>My Account</h5><p>My Product<br>My Orders<br>My Address<br>My Personal Info</p></div>
<div class="abs col" style="left:581px;top:1062px"><h5>Make a Payment</h5></div>
<div class="abs pay" style="left:581px;top:1089px;background:#f3e3cf"></div>
<div class="abs pay" style="left:613px;top:1089px;background:#8fc3e8"></div>
<div class="abs pay" style="left:646px;top:1089px;background:#2a4a9c"></div>
<div class="abs pay" style="left:581px;top:1112px;background:#e9eef5"></div>
<div class="abs pay" style="left:613px;top:1112px;background:#d9452a"></div>
<div class="abs pay" style="left:646px;top:1112px;background:#333"></div>
<div class="abs rule"></div>
<div class="abs copy">Copyright © 2014 &nbsp;Dusty Spur Outfitters . All rights reserved.</div>
<div class="abs soc" style="left:584px;background:#3b5aa0"></div>
<div class="abs soc" style="left:601px;background:#2aa3dd"></div>
<div class="abs soc" style="left:618px;background:#1f6fa8"></div>
<div class="abs soc" style="left:635px;background:#d4302a"></div>
<div class="abs soc" style="left:652px;background:#ee7b22"></div>
<div class="abs soc" style="left:669px;background:#d84a36"></div>
</body>
</html>
```